Website Design for Agency

We require a website for our new agency. We have created a brief with our content, copywriting and most graphical assets. We just need some great with layout and to add some flair.

Number of Pages Required

1 page

Font styles to use
Sans Serif

```html
<!DOCTYPE html>
<html lang="en">
<head>
<meta charset="utf-8">
<title>Storyproof Partners</title>
<link href="https://fonts.googleapis.com/css2?family=Poppins:wght@400;500;600;700&family=Open+Sans:wght@400;600&display=swap" rel="stylesheet">
<style>
:root{
  --ink:#1f1f1f;
  --text:#3c3c3c;
  --paper:#ffffff;
  --line:#cfcfcf;
  --art:#ececec;
  --art2:#f6f6f6;
  --deco:#f1f1f1;
}
*{box-sizing:border-box;margin:0;padding:0}
html,body{width:1200px;height:4914px;overflow:hidden;background:var(--paper)}
body{position:relative;font-family:"Open Sans",sans-serif;color:var(--text)}
.abs{position:absolute}
h1,h2,h3,.brand{font-family:"Poppins",sans-serif;color:var(--ink)}
h1{font-size:41px;line-height:50px;font-weight:600;letter-spacing:-0.4px}
h2{font-size:34px;line-height:49px;font-weight:600;letter-spacing:-0.5px}
p.body{font-size:14.5px;line-height:30px;text-align:justify}
.btn{display:inline-block;font-size:14px;padding:8px 20px;border-radius:22px;border:2px solid var(--ink);color:var(--ink);background:var(--paper);margin-right:24px}
.btn.dark{background:var(--ink);color:#fff}
.art{background:linear-gradient(160deg,var(--art2),var(--art));border-radius:12px}
.deco{position:absolute;background:var(--deco);border-radius:8px}
.nav{top:30px;left:110px;width:980px;display:flex;justify-content:space-between;align-items:center}
.brand{font-size:28px;font-weight:500}
.menu{display:flex;gap:27px;font-size:15px;color:var(--text)}
.menu .on{color:var(--ink);font-weight:600}
.logos{top:690px;left:110px;width:980px;display:flex;justify-content:space-between;align-items:center;font-family:"Poppins",sans-serif;font-weight:600;font-size:17px;color:#444}
.band{background:var(--ink);border-radius:14px;color:#fff;text-align:center}
.band h2{color:#fff}
.band .btn{border-color:#fff}
.timeline{left:601px;top:3470px;width:490px;border-left:2px solid var(--line);padding-left:30px}
.dot{position:absolute;left:-7px;width:12px;height:12px;border-radius:50%;background:var(--ink)}
.card{position:absolute;width:229px;height:280px;border:1.5px solid var(--line);border-radius:16px;padding:40px 22px;background:#fff}
.card h3{font-size:20px;font-weight:500;margin-bottom:20px}
.card p{font-size:14px;line-height:30px}
.card .ring{position:absolute;right:-2px;top:-4px;width:46px;height:46px;border-radius:50%;background:#e8e8e8}
.card.raised{box-shadow:0 10px 30px rgba(0,0,0,.12);border-color:#eee}
.footer{top:4560px;left:110px;width:980px;height:305px;color:#fff;text-align:center}
.footer .fbrand{color:#fff;font-size:25px;padding-top:60px}
.footer .fmenu{display:flex;justify-content:center;gap:50px;font-size:16px;margin-top:22px}
.footer .social{display:flex;justify-content:center;gap:26px;font-size:15px;margin-top:24px;font-family:"Open Sans",sans-serif}
.footer .social span{display:flex;align-items:center;gap:7px}
.footer .social span::before{content:"";width:9px;height:9px;border-radius:50%;background:#fff}
.footer small{display:block;font-size:15px;margin-top:26px}
</style>
</head>
<body>

<div class="abs" style="left:1090px;top:-60px;width:120px;height:80px;border-radius:50%;background:var(--ink)"></div>
<div class="abs" style="left:-60px;top:760px;width:80px;height:160px;border-radius:50%;background:var(--ink)"></div>
<div class="abs" style="left:1170px;top:3240px;width:80px;height:170px;border-radius:50%;background:var(--ink)"></div>
<div class="deco" role="img" aria-label="Decorative dot grid" style="left:1110px;top:370px;width:90px;height:150px"></div>
<div class="deco" role="img" aria-label="Decorative dot grid" style="left:0;top:2360px;width:80px;height:160px"></div>
<div class="deco" role="img" aria-label="Decorative dot grid" style="left:1090px;top:4450px;width:110px;height:170px"></div>
<div class="deco" role="img" aria-label="Decorative pixel squares" style="left:0;top:0;width:70px;height:75px"></div>
<div class="deco" role="img" aria-label="Decorative pixel squares" style="left:1080px;top:2000px;width:120px;height:115px"></div>
<div class="deco" role="img" aria-label="Decorative pixel squares" style="left:0;top:4505px;width:58px;height:52px"></div>

<header class="abs nav">
  <div class="brand">Storyproof Partners</div>
  <nav class="menu"><span class="on">Home</span><span>Services</span><span>How it works</span><span>Examples</span><span>Contact</span></nav>
</header>

<section class="abs" style="left:110px;top:140px;width:492px">
  <h1>Win More Hearts with Powerful Case Studies</h1>
  <p class="body" style="margin-top:18px">Testimonial Videos, written PDF's, slides, one-pagers and social media content. We create spellbinding case study stories and videos that will drive business for your revenue team . No more writing, proofing organizing videographers and time-consuming hassles. We'll handle everything 100% and deliver to you powerful marketing assets you'll be proud to share.</p>
  <div style="margin-top:26px"><span class="btn dark">Learn More</span><span class="btn">Watch Video</span></div>
</section>
<div class="abs art" role="img" aria-label="Line illustration of a person riding a rising arrow chart" style="left:680px;top:134px;width:380px;height:362px"></div>

<h3 class="abs" style="left:0;width:1200px;top:610px;text-align:center;font-size:16px;font-weight:600">Trusted by hundreds of top companies</h3>
<div class="abs logos"><span>Orbitone</span><span>Kelva</span><span>Norvane</span><span>Meridian Health</span><span>Harbor Funds</span><span>Strideline</span><span>Cedrova</span></div>

<div class="abs art" role="img" aria-label="Line illustration of a person working at a laptop surrounded by social icons" style="left:114px;top:820px;width:390px;height:296px"></div>
<section class="abs" style="left:601px;top:852px;width:495px">
  <h2>Capture results, built trust and win new business</h2>
  <p class="body" style="margin-top:16px;width:490px">Combining real-world results with social proof, one well-produced customer story with multiple marketing assets will do a LOT of the heavy lifting for your business sales...because it comes directly from the mouth of a happy human who loves what you do.</p>
</section>

<section class="abs" style="left:110px;top:1225px;width:492px">
  <h2>It's More Than Marketing</h2>
  <p class="body" style="margin-top:16px">No more awful sales sheets and dull corporate announcements that tell people to spend their money without reason. Our team of Laurel® -winning journalists ensure your case studies are authentic. They're real. They're raw. They give people a reason to trust you, and, more importantly, a reason to give you their business.</p>
</section>
<div class="abs art" role="img" aria-label="Line illustration of two people sharing reactions on a tablet" style="left:735px;top:1154px;width:355px;height:353px"></div>

<section class="abs band" style="left:110px;top:1587px;width:980px;height:328px;padding:50px 60px">
  <h2>Get a testimonial video anywhere nationwide</h2>
  <p style="font-size:14.5px;line-height:30px;margin-top:18px">You get our team of pros to handle the outreach, the interviews, the field production (or remote) and all the editing, graphics and storytelling for a lot less than you think. Powerful, proven content that moves the needle.</p>
  <div style="margin-top:28px"><span class="btn">Plans and Pricing</span><span class="btn dark" style="margin-right:0">Learn More</span></div>
</section>

<section class="abs" style="left:110px;top:2040px;width:540px">
  <h2>Don't settle for just a single case study. Get a lot more.</h2>
  <p class="body" style="margin-top:16px;width:492px">Narrative stories with your customer as the hero is key to readability and persuasion. Get professionally wordsmithed case studies to upload to your website, social channels, and more with pride.</p>
  <div style="margin-top:28px"><span class="btn dark">Plans and Pricing</span><span class="btn">Learn More</span></div>
</section>
<div class="abs art" role="img" aria-label="Line illustration of a person typing with a large pen writing on a page" style="left:705px;top:1994px;width:370px;height:372px"></div>

<div class="abs art" role="img" aria-label="Line illustration of two people presenting charts on a board" style="left:114px;top:2432px;width:320px;height:325px"></div>
<section class="abs" style="left:601px;top:2485px;width:490px">
  <h2>Promo &amp; Sales Collateral</h2>
  <p class="body" style="margin-top:16px">From one-sheets, slides, long, short, and ultra-short articles for your website, blog, or sales team. You are in good hands knowing the content you get back is marketing gold. All without the headaches.</p>
  <div style="margin-top:26px"><span class="btn dark">Plans and Pricing</span></div>
</section>

<section class="abs" style="left:110px;top:2835px;width:560px">
  <h2>Need help promoting your customer story? We got you.</h2>
  <p class="body" style="margin-top:16px;width:492px">You get campaign level help from our team. Landing pages, lead capture forms, press releases &amp; PR outreach to 400+ organizations and 100,000 journalists. All done by former our in-house former reporters who know how it's done.</p>
  <div style="margin-top:26px"><span class="btn dark">Plans and Pricing</span><span class="btn">Learn More</span></div>
</section>
<div class="abs art" role="img" aria-label="Line illustration of a team meeting around a table with a screen" style="left:690px;top:2850px;width:400px;height:290px"></div>

<h2 class="abs" style="left:250px;width:700px;top:3280px;text-align:center">100% stress-free case study project management</h2>
<div class="abs art" role="img" aria-label="Line illustration of a person relaxing with a laptop under a palm tree at the beach" style="left:105px;top:3405px;width:382px;height:373px"></div>
<div class="abs timeline">
  <div class="dot" style="top:8px"></div>
  <h3 style="font-size:31px;font-weight:600">Get More for Less</h3>
  <p class="body" style="margin-top:10px">Whether you manage the marketing yourself or or have an in-house marketing manager, getting case studies done can be time consuming and costly if you don't do it right. We believe partnering with a case study expert can help your business prosper and establish itself as an industry leader.</p>
  <div class="dot" style="top:264px;width:8px;height:8px;left:-5px"></div>
  <h3 style="font-size:31px;font-weight:600;margin-top:36px">Free up your schedule</h3>
</div>

<h2 class="abs" style="left:180px;width:840px;top:3898px;text-align:center">Everything you need is right here. Avoid the headaches over case study copywriting and testimonial video production. Get in touch</h2>
<div class="abs" style="left:0;width:1200px;top:4090px;text-align:center"><span class="btn dark" style="margin:0">Plans and Pricing</span></div>

<div class="card" style="left:110px;top:4207px"><div class="ring"></div><h3>Pricing Plan 1</h3><p>Lorem ipsum dolor sitrt amet, conse adipiscing elit, sed do eius tempor incididunt ut let dolore magna aliqua.</p></div>
<div class="card" style="left:361px;top:4207px"><h3>Pricing Plan 2</h3><p>Lorem ipsum dolor sitrt amet, conse adipiscing elit, sed do eius tempor incididunt ut let dolore magna aliqua.</p></div>
<div class="card raised" style="left:611px;top:4175px"><div class="ring" style="background:none;border:6px solid #e8e8e8;width:40px;height:40px;top:40px;right:14px"></div><h3>Pricing Plan 3</h3><p>Lorem ipsum dolor sitrt amet, conse adipiscing elit, sed do eius tempor incididunt ut let dolore magna aliqua.</p></div>
<div class="card" style="left:861px;top:4207px"><h3>Pricing Plan 4</h3><p>Lorem ipsum dolor sitrt amet, conse adipiscing elit, sed do eius tempor incididunt ut let dolore magna aliqua.</p></div>

<footer class="abs band footer">
  <div class="brand fbrand">Storyproof Partners</div>
  <nav class="fmenu"><span>Home</span><span>Services</span><span>How it works</span><span>Examples</span><span>Contact</span></nav>
  <div class="social"><span>Facet</span><span>Viewly</span><span>Chirpa</span><span>Lumo</span><span>Pinora</span><span>Worklink</span></div>
  <small>2022 Storyproof Partners. All Rights Reserved.</small>
</footer>

</body>
</html>
```